Business card for Luxury Portable Restroom Trailer company

We are a Luxury Portable Restroom Trailer Company Called FALCRIDGE HIRES. Based in Orange County California. We provide portable restroom trailers for events, such as, Weddings, Concerts, Charity events, Sporting events, Tournaments, Corporate events, ect. We rent and Sell the Luxury restrooms. Our colors are white, grey, and Orange. As you will see in the logo we uploaded.
There are 2 people in the company so the names and titles will change for the 3 people but card will remain the same. Here is the information for each Person: Dwight Penner CFO 555 318-0476
next Person: Leon Marchetti VP 555 318-0476
Next Person: Owen Marchetti CEO 555 318-0476
Information to include on the card: Luxury Restroom Trailers Rental and Sales. Weddings, Concerts, Charity, Sporting and Corp. Events.

```html
<!DOCTYPE html>
<html lang="en">
<head>
<meta charset="utf-8">
<title>Falcridge Hires – Business Card</title>
<link href="https://fonts.googleapis.com/css2?family=Open+Sans:wght@400;600;700;800&display=swap" rel="stylesheet">
<style>
  :root {
    --stage: #232323;
    --orange: #f26b21;
    --orange-light: #f5813a;
    --orange-deep: #e85d14;
    --charcoal: #252527;
    --charcoal-soft: #2e2b2b;
    --grey: #8a8a8c;
    --white: #ffffff;
  }
  * { box-sizing: border-box; margin: 0; padding: 0; }
  html, body {
    width: 1200px; height: 768px; overflow: hidden;
    background: var(--stage);
    font-family: "Open Sans", Arial, sans-serif;
  }
  .stage {
    width: 1200px; height: 768px;
    display: flex; align-items: center; justify-content: center; gap: 40px;
  }
  .card {
    position: relative;
    width: 540px; height: 310px;
    border-radius: 22px;
    overflow: hidden;
  }

  /* Front */
  .card-front { background: var(--orange); }
  .front-texture {
    position: absolute; inset: 0;
    background: linear-gradient(135deg, var(--orange-deep) 0%, var(--orange-light) 50%, var(--orange) 100%);
  }
  .front-brand {
    position: absolute; right: 44px; bottom: 92px;
    display: flex; align-items: center; gap: 10px;
  }
  .brand-mark { width: 14px; height: 14px; background: var(--white); }
  .brand-name {
    font-weight: 800; font-size: 26px; letter-spacing: 1px;
    color: var(--white);
  }

  /* Back */
  .card-back {
    background: var(--charcoal);
    border-bottom: 6px solid var(--orange);
  }
  .back-silhouette {
    position: absolute; left: 150px; top: -20px; width: 330px; height: 340px;
    background: radial-gradient(ellipse at 55% 55%, var(--charcoal-soft) 0%, var(--charcoal-soft) 45%, rgba(37,37,39,0) 72%);
  }
  .back-brand {
    position: absolute; left: 28px; top: 30px;
    display: flex; align-items: center; gap: 10px;
  }
  .back-brand .brand-mark { background: var(--orange); }
  .back-brand .brand-name { color: var(--orange); font-size: 24px; }

  .person {
    position: absolute; right: 0; top: 30px;
    display: flex; align-items: stretch; gap: 10px;
  }
  .person-text { text-align: right; padding-top: 2px; }
  .person-name { color: var(--orange); font-weight: 700; font-size: 22px; line-height: 1.1; }
  .person-title { color: var(--white); font-size: 11px; font-weight: 600; letter-spacing: .5px; }
  .person-bar { width: 12px; background: var(--orange); }

  .contact {
    position: absolute; left: 30px; top: 128px;
    list-style: none; color: var(--white); font-size: 12.5px;
  }
  .contact li { display: flex; align-items: center; gap: 9px; height: 20px; }
  .contact svg { width: 12px; height: 12px; fill: var(--orange); flex: none; }

  .services {
    position: absolute; left: 30px; right: 30px; bottom: 22px;
    color: var(--white); font-size: 12.5px; line-height: 1.7;
  }
  .services p { display: flex; flex-wrap: wrap; align-items: center; gap: 4px 8px; }
  .services p:first-child { padding-left: 40px; }
  .bullet { display: inline-block; width: 7px; height: 7px; background: var(--orange); }
</style>
</head>
<body>
<main class="stage">

  <section class="card card-front" aria-label="Card front">
    <div class="front-texture" role="img" aria-label="Orange background with a repeating brand-symbol texture"></div>
    <div class="front-brand">
      <span class="brand-mark"></span>
      <span class="brand-name">FALCRIDGE HIRES</span>
    </div>
  </section>

  <section class="card card-back" aria-label="Card back">
    <div class="back-silhouette" role="img" aria-label="Faint large animal silhouette in dark grey"></div>

    <div class="back-brand">
      <span class="brand-mark"></span>
      <span class="brand-name">FALCRIDGE HIRES</span>
    </div>

    <div class="person">
      <div class="person-text">
        <div class="person-name">Dwight Penner</div>
        <div class="person-title">CFO</div>
      </div>
      <div class="person-bar"></div>
    </div>

    <ul class="contact">
      <li>
        <svg viewBox="0 0 24 24"><path d="M6.6 10.8a15 15 0 0 0 6.6 6.6l2.2-2.2a1 1 0 0 1 1-.25 11.4 11.4 0 0 0 3.6.57 1 1 0 0 1 1 1V20a1 1 0 0 1-1 1A17 17 0 0 1 3 4a1 1 0 0 1 1-1h3.5a1 1 0 0 1 1 1c0 1.25.2 2.45.57 3.57a1 1 0 0 1-.25 1z"/></svg>
        555 318-0476
      </li>
      <li>
        <svg viewBox="0 0 24 24"><path d="M2 5h20v14H2z M4 7v.5l8 5 8-5V7z" fill-rule="evenodd"/></svg>
        info@falcridgehires.com
      </li>
      <li>
        <svg viewBox="0 0 24 24"><path d="M12 2a10 10 0 1 0 0 20 10 10 0 0 0 0-20zm0 2c.9 1.2 1.6 2.6 2 4h-4c.4-1.4 1.1-2.8 2-4zM4.3 14a8 8 0 0 1 0-4h3.4a16 16 0 0 0 0 4zm5.7 0a14 14 0 0 1 0-4h4a14 14 0 0 1 0 4zm6.3 0a16 16 0 0 0 0-4h3.4a8 8 0 0 1 0 4zM12 20c-.9-1.2-1.6-2.6-2-4h4c-.4 1.4-1.1 2.8-2 4z"/></svg>
        www.falcridgehires.com
      </li>
    </ul>

    <div class="services">
      <p><span class="bullet"></span>Luxury Restroom Trailers Rental and Sales</p>
      <p>
        <span class="bullet"></span>Weddings
        <span class="bullet"></span>Concerts
        <span class="bullet"></span>Charity
        <span class="bullet"></span>Sporting and Corp
        <span class="bullet"></span>Events
      </p>
    </div>
  </section>

</main>
</body>
</html>
```